Fine Art business needs new website

We need a simple website with a home page, about us page, New sculptures, Sold sculptures, and a contact us page.Our sculptures are very high end one of a kind pieces. As such we need the site to be VERY elegant and professional. Lastly, because I'll be updating pictures on the website on a monthly basis it needs to be user friendly to update (Wordpress is preferred). The only branding we have so far for the business is a business card.
Updates
I wasn't completely ready when this project launched, also I am on the road right now and haven't been able to be as responsive to all you designers as I would like. I will work on giving feedback to all the top designs we've received so far. Thank you all so much for your participation and hardwork.
Target Market(s)
High end customers (affluent), art collectors, interior decorators/designers
Industry/Entity Type
Art Gallery
Coding
Coded - Design and coding required
Number of Pages Required
5+ page
Requirements
Must have
- Easily editable picture gallery for myself so that I can add new pieces(pictures of the pieces), remove sold pieces, etc. I would like the website to be built in wordpress so I can update it. I currently use mangewordpress through Netmarro for my other business website and would like to do the same for this one.
- Pages:
- -Intro page with featured pieces
- -Current pieces gallery (for sale) mainly a picture gallery
- -Sculptures archive (sold pieces) another picture gallery
- -About us: Pull-down of -about the artist (attached content)
- -Artistic Process (attached content)
- -Show Schedule:
- -one page dedicated to "friends of TMV" (basically a link page)
- TO BE CLEAR "www.pineroverslane.com" IS A TOTALLY DIFFERENT SITE AND I'M NOT TRYING TO COMBINE THE TWO OR JOIN THEM INTO ONE. This page needs be more elegant and seperate from The Pine Rovers site.
- UPDATE: I'd like a link to the TMV Faceplume page: https://www.faceplume-social.com/mirelcraftworks/
Nice to have
- I would like the pictures on the gallery pages able to have text connected with them (Materials, price)
- I would like the site style and fonts to be similar to our business cards we've already had designed (picture attached).
Should not have
- Too much flash or other things that will make the site slow to load.

```html
<!DOCTYPE html>
<html lang="en">
<head>
<meta charset="utf-8">
<title>TMV – Featured Sculptures</title>
<link href="https://fonts.googleapis.com/css2?family=Lato:wght@300;400;700&family=Libre+Baskerville&display=swap" rel="stylesheet">
<style>
:root{
  --ink:#2b2b2b;
  --muted:#444;
  --page:#f5f5f5;
  --bar:#000;
  --foot:#232323;
  --accent:#5c5296;
  --rule:#bcbcbc;
  --white:#fff;
}
*{margin:0;padding:0;box-sizing:border-box}
html,body{width:1200px;height:1108px;overflow:hidden}
body{background:var(--page);font-family:'Lato',sans-serif;color:var(--ink);position:relative}
.topbar{position:absolute;left:0;top:0;width:1200px;height:75px;background:var(--bar)}
.nav{position:absolute;left:192px;top:27px;display:flex;gap:21px;list-style:none}
.nav a{color:var(--white);text-decoration:none;font-size:14.5px;font-weight:400;display:flex;align-items:center;gap:6px;padding:0 4px 8px}
.nav .active{border-bottom:2px solid var(--accent)}
.menu-toggle{position:absolute;left:968px;top:27px;width:35px}
.menu-toggle span{display:block;height:3px;background:var(--white);margin-bottom:4px}
.section-title{position:absolute;left:0;width:1200px;top:114px;text-align:center;font-family:'Libre Baskerville',serif;font-size:27px;font-weight:400;color:var(--ink)}
.rule{position:absolute;height:1px;background:var(--rule)}
.card{position:absolute;top:216px;width:213px;height:274px;box-shadow:0 3px 6px rgba(0,0,0,.35)}
.card-amethyst{left:227px;background:radial-gradient(ellipse at 50% 45%,#4a3a78 0%,#231c33 35%,#141414 70%)}
.card-drusy{left:493px;background:radial-gradient(ellipse at 50% 40%,#4a3a33 0%,#221b18 38%,#131313 72%)}
.card-spiral{left:758px;background:radial-gradient(ellipse at 50% 45%,#8a5a2c 0%,#3a2614 38%,#141414 72%)}
.gallery-btn{position:absolute;left:544px;top:396px;width:112px;height:43px;border:2px solid var(--white);border-radius:3px;color:var(--white);font-size:11px;font-weight:700;display:flex;align-items:center;justify-content:center;background:rgba(0,0,0,.35)}
.to-top{position:absolute;left:1026px;top:397px;width:34px;height:34px;border:1.5px solid #222;display:flex;align-items:center;justify-content:center}
.dots{position:absolute;top:533px;left:563px;display:flex;gap:21px}
.dots span{width:11px;height:11px;border-radius:50%;border:1.3px solid #111}
.dots .on{background:#111}
.more-gallery{position:absolute;left:0;width:1200px;top:568px;text-align:center;color:var(--accent);font-size:14px;font-weight:300;display:flex;justify-content:center;align-items:center;gap:14px}
.more-gallery b{font-weight:700}
.feature{position:absolute;top:690px;width:220px}
.feature h2{font-size:19px;font-weight:400;text-align:center;color:var(--ink);height:30px}
.feature .under{width:116px;height:1px;background:var(--rule);margin:4px auto 0}
.feature p{font-size:12.2px;font-weight:300;line-height:25.7px;color:var(--muted);margin-top:16px;letter-spacing:.2px}
.feature .see{display:flex;align-items:center;gap:9px;font-size:12.5px;font-weight:400;margin-top:5px;color:var(--ink)}
.footer{position:absolute;left:0;top:897px;width:1200px;height:211px;background:var(--foot);color:var(--white)}
.footer h3{position:absolute;top:40px;font-size:22px;font-weight:700;letter-spacing:-.3px}
.footer .col{position:absolute;top:72px;font-size:13px;line-height:21.5px}
.contact-list{list-style:none}
.contact-list li{display:flex;align-items:center;gap:8px}
.contact-list .plain{padding-left:23px;font-weight:700}
.social{display:flex;gap:9px;font-size:11px}
.social span{display:flex;align-items:center;gap:4px}
.social i{width:9px;height:9px;background:#2a7bc0;display:inline-block}
</style>
</head>
<body>
<header class="topbar">
  <ul class="nav">
    <li><a class="active" href="#">HOME</a></li>
    <li><a href="#">ABOUT <svg width="10" height="6" viewBox="0 0 10 6"><path d="M1 1l4 4 4-4" stroke="#fff" fill="none" stroke-width="1.2"/></svg></a></li>
    <li><a href="#">GALLERY</a></li>
    <li><a href="#">CONTACT</a></li>
  </ul>
  <div class="menu-toggle"><span></span><span></span><span></span></div>
</header>

<h1 class="section-title">Featured Sculptures</h1>
<div class="rule" style="left:519px;top:163px;width:162px"></div>

<div class="card card-amethyst" role="img" aria-label="Amethyst geode sculpture on a wooden base"></div>
<div class="card card-drusy" role="img" aria-label="Drusy quartz stone sculpture on a wooden base"></div>
<div class="card card-spiral" role="img" aria-label="Polished spiral stone sculpture with ammonite"></div>
<div class="gallery-btn">SEE GALLERY</div>

<div class="to-top"><svg width="18" height="10" viewBox="0 0 18 10"><path d="M1 9l8-8 8 8" stroke="#222" fill="none" stroke-width="1.3"/></svg></div>

<div class="dots"><span class="on"></span><span></span><span></span></div>

<div class="more-gallery">SEE MORE FROM THE <b>GALLERY</b>
  <svg width="22" height="12" viewBox="0 0 22 12"><path d="M0 6h20M15 1l5 5-5 5M0 3.5h17" stroke="#5c5296" fill="none" stroke-width="1"/></svg>
</div>

<div class="rule" style="left:214px;top:642px;width:772px"></div>

<section class="feature" style="left:214px">
  <h2>Meet The Artists</h2><div class="under"></div>
  <p>Meet the people behind these beautiful masterpiece, their biography and the history of the Marlowe's.</p>
  <div class="see">SEE MORE <svg width="20" height="10" viewBox="0 0 20 10"><path d="M0 5h19M14 1l4 4-4 4" stroke="#333" fill="none" stroke-width="1"/></svg></div>
</section>
<section class="feature" style="left:492px">
  <h2>The Artistic Process</h2><div class="under"></div>
  <p>Discover each detail of the artistic process of the creation of these fine sculptures from base to perfect.</p>
  <div class="see">SEE MORE <svg width="20" height="10" viewBox="0 0 20 10"><path d="M0 5h19M14 1l4 4-4 4" stroke="#333" fill="none" stroke-width="1"/></svg></div>
</section>
<section class="feature" style="left:770px;top:693px">
  <h2>The Pine Rovers</h2><div class="under"></div>
  <p>Find out more about Slate Hollow Studio's sister site, The Pine Rovers. Lorem Ipsum dolor.</p>
  <div class="see">SEE MORE <svg width="20" height="10" viewBox="0 0 20 10"><path d="M0 5h19M14 1l4 4-4 4" stroke="#333" fill="none" stroke-width="1"/></svg></div>
</section>

<footer class="footer">
  <h3 style="left:198px">ABOUT US</h3>
  <p class="col" style="left:196px;width:220px">This is a dummy text just to provide text in the About Us section which will be added correctly later on.</p>

  <h3 style="left:526px">OUR ADDRESS</h3>
  <ul class="col contact-list" style="left:526px">
    <li><svg width="15" height="15" viewBox="0 0 15 15"><path d="M3 1l3 3-1.5 2c1 2 2.5 3.5 4.5 4.5L11 9l3 3-2 2C6 13 2 9 1 3z" fill="#fff"/></svg>(555) 014-2290</li>
    <li><svg width="15" height="15" viewBox="0 0 15 15"><rect x="1" y="3" width="13" height="9" fill="none" stroke="#fff"/><path d="M1 3l6.5 5 6.5-5M1 12l5-4M14 12l-5-4" stroke="#fff" fill="none"/></svg>info@pineroverslane.com</li>
    <li><svg width="15" height="15" viewBox="0 0 15 15"><path d="M6 9l3-3M5 7L3 9a2 2 0 003 3l2-2M10 8l2-2a2 2 0 00-3-3L7 5" stroke="#fff" fill="none" stroke-width="1.2"/></svg>www.mirelcraftworks.com</li>
    <li class="plain">CONTACT US</li>
  </ul>

  <h3 style="left:853px">KEEP IN TOUCH</h3>
  <div class="col social" style="left:858px;top:82px">
    <span><i></i>Flit</span><span><i></i>Pinly</span><span><i></i>Faceplume</span><span><i></i>Snapgram</span>
  </div>
</footer>
</body>
</html>
```